Stylish business cards for KV7

To create an appealing and professional business card design for a WOMEN Owned Construction Supply Company.
2 sided card. Incorporate brand elements, curvy, colorful, sleek and bright. No solid white background. attached samples of styles added shapes/ribbons. Want something with that WOW that looks awesome, factor. It is a new logo, so feel free to mess with logo colors in the blue and teal factors that can look good with both dark and light background. If you want to try a watermark with just the KV7, without the "Supply" that might look cool to.

Industry/Entity Type

Women owned construction supply company

Contact Information for Business Card

Name, Title, and phone number and email, web page. maybe spot for qr code.

Font styles to use
Sans Serif

Requirements
Nice to have
• would love to see colors, maybe stylish ribbon dividers or some sort of 2 or 3 tone color card that compliments logo.
Should not have
• Please do not have all white background. Do not include Home/reale state/ or building images.

```html
<!DOCTYPE html>
<html lang="en">
<head>
<meta charset="utf-8">
<title>KV7 Supply – Business Cards</title>
<link href="https://fonts.googleapis.com/css2?family=Montserrat:wght@400;500;700&display=swap" rel="stylesheet">
<style>
  :root {
    --page-bg: #2a2b2d;
    --card-bg: #141516;
    --silver: #c9cbcd;
    --brand-blue: #1f8fc0;
    --brand-navy: #1e4f7e;
    --text-light: #e8e9ea;
    --divider: #1f8fc0;
  }
  * { margin: 0; padding: 0; box-sizing: border-box; }
  html, body {
    width: 1200px;
    height: 874px;
    overflow: hidden;
    background: var(--page-bg);
    font-family: "Montserrat", sans-serif;
  }
  .canvas {
    position: relative;
    width: 1200px;
    height: 874px;
  }
  .card {
    position: absolute;
    left: 250px;
    width: 700px;
    height: 400px;
    background: var(--card-bg);
    border-radius: 22px;
    box-shadow: 0 10px 30px rgba(0,0,0,0.45);
  }
  .card--front { top: 17px; }
  .card--back { top: 457px; }

  .wordmark {
    position: absolute;
    font-weight: 700;
    letter-spacing: 1px;
    white-space: nowrap;
  }
  .card--front .wordmark {
    left: 0; right: 0;
    top: 160px;
    text-align: center;
    font-size: 58px;
    color: var(--silver);
  }
  .card--back .wordmark {
    left: 40px;
    top: 170px;
    font-size: 46px;
    color: var(--brand-blue);
  }

  .divider {
    position: absolute;
    left: 355px;
    top: 70px;
    width: 3px;
    height: 260px;
    background: var(--divider);
  }

  .contact {
    position: absolute;
    left: 385px;
    top: 72px;
    color: var(--text-light);
  }
  .contact__name {
    font-size: 28px;
    font-weight: 700;
    color: var(--brand-blue);
    letter-spacing: 1px;
  }
  .contact__title {
    font-size: 17px;
    font-weight: 500;
    margin-top: 2px;
  }
  .contact__address {
    font-size: 17px;
    line-height: 1.35;
    margin-top: 22px;
  }
  .contact__list {
    list-style: none;
    margin-top: 18px;
    font-size: 17px;
    line-height: 1.65;
  }
  .contact__list li {
    display: flex;
    align-items: center;
    gap: 10px;
  }
  .contact__list svg {
    width: 15px;
    height: 15px;
    fill: var(--brand-blue);
    flex: none;
  }
</style>
</head>
<body>
<main class="canvas">
  <section class="card card--front" aria-label="Card front">
    <div class="wordmark">KV7 Supply</div>
  </section>

  <section class="card card--back" aria-label="Card back">
    <div class="wordmark">KV7 Supply</div>
    <div class="divider"></div>
    <div class="contact">
      <p class="contact__name">NORA HALVEY</p>
      <p class="contact__title">Managing Director</p>
      <p class="contact__address">Your address, City<br>State, Zip 1234</p>
      <ul class="contact__list">
        <li>
          <svg viewBox="0 0 24 24" aria-hidden="true"><path d="M6.6 10.8a15.1 15.1 0 0 0 6.6 6.6l2.2-2.2a1 1 0 0 1 1-.25 11.4 11.4 0 0 0 3.6.57 1 1 0 0 1 1 1V20a1 1 0 0 1-1 1A17 17 0 0 1 3 4a1 1 0 0 1 1-1h3.5a1 1 0 0 1 1 1c0 1.25.2 2.45.57 3.6a1 1 0 0 1-.25 1z"/></svg>
          123 456 789
        </li>
        <li>
          <svg viewBox="0 0 24 24" aria-hidden="true"><path d="M2 5h20v14H2z M2 5l10 8 10-8" stroke="#141516" stroke-width="1.5"/></svg>
          info@kv7supply.com
        </li>
        <li>
          <svg viewBox="0 0 24 24" aria-hidden="true"><circle cx="12" cy="12" r="10"/><path d="M2 12h20M12 2c3 3 3 17 0 20M12 2c-3 3-3 17 0 20" stroke="#141516" stroke-width="1.5" fill="none"/></svg>
          www.kv7supply.com
        </li>
      </ul>
    </div>
  </section>
</main>
</body>
</html>
```